Create a cover for English Grammar Workbook

This book describes a system to learn English in a proper way - we call it The ''Lantern Row'' System.

It focuses on not only teaching grammar and its structures, but also giving students tips on how to use it and the best ways to remember what they learn.

The cover should have 3 realistic pillars (3D), with one closer to the front to show that this book is the 1st (front) Pillar.

The title is: "Building Sentences That Stick: *A Friendly Path Through Usage"*

Author's name: Doreen Calloway

```html
<!DOCTYPE html>
<html lang="en">
<head>
<meta charset="utf-8">
<title>Building Sentences That Stick — Cover</title>
<link rel="stylesheet" href="https://fonts.googleapis.com/css2?family=Sacramento&family=Oswald:wght@600&family=Noto+Serif:wght@400&family=Montserrat:wght@700&display=swap">
<style>
  :root {
    --page: #ffffff;
    --cover: #3b3b3b;
    --red: #cc1419;
    --white: #ffffff;
    --stone-light: #f4f4f4;
    --stone-mid: #d9d9d9;
    --stone-dark: #a4a4a4;
    --stone-shade: rgba(0, 0, 0, 0.18);
  }
  * { margin: 0; padding: 0; box-sizing: border-box; }
  html, body {
    width: 1200px; height: 843px; overflow: hidden;
    background: var(--page);
  }
  .cover {
    position: absolute;
    left: 357px; top: 67px;
    width: 496px; height: 704px;
    background: var(--cover);
    overflow: hidden;
    box-shadow: 0 6px 24px rgba(0, 0, 0, 0.12);
  }
  .title { font-weight: normal; }
  .title-script {
    position: absolute; top: 18px; left: 0; width: 100%;
    text-align: center;
    font-family: "Sacramento", cursive;
    font-size: 74px; line-height: 1;
    color: var(--white);
  }
  .title-main {
    position: absolute; left: 0; width: 100%;
    text-align: center;
    font-family: "Oswald", sans-serif;
    font-weight: 600;
    font-size: 74px; line-height: 1;
    letter-spacing: 4px;
    color: var(--red);
  }
  .title-main.line-one { top: 86px; }
  .title-main.line-two { top: 166px; }
  .subtitle {
    position: absolute; left: 64px; top: 253px;
    width: 368px; height: 38px;
    border: 2px solid var(--red);
    display: flex; align-items: center; justify-content: center;
    font-family: "Noto Serif", serif;
    font-size: 19px; letter-spacing: 0.5px;
    color: var(--white);
  }
  .pillar {
    position: absolute;
    border-radius: 3px;
    background:
      linear-gradient(180deg, rgba(255,255,255,0.15) 0%, rgba(0,0,0,0) 30%, var(--stone-shade) 100%),
      linear-gradient(90deg, var(--stone-dark) 0%, var(--stone-light) 42%, var(--stone-mid) 75%, var(--stone-dark) 100%);
  }
  .pillar.left   { left: 20px;  top: 400px; width: 110px; height: 246px; }
  .pillar.center { left: 172px; top: 302px; width: 155px; height: 344px; }
  .pillar.right  { left: 350px; top: 369px; width: 122px; height: 277px; }
  .author-band {
    position: absolute; left: 0; bottom: 0;
    width: 100%; height: 58px;
    background: var(--red);
    display: flex; align-items: center; justify-content: center;
    font-family: "Montserrat", sans-serif;
    font-weight: 700; font-size: 26px;
    letter-spacing: 5px;
    color: var(--white);
  }
</style>
</head>
<body>
  <main class="cover">
    <h1 class="title">
      <span class="title-script">Building</span>
      <span class="title-main line-one">SENTENCES</span>
      <span class="title-main line-two">THAT STICK</span>
    </h1>
    <p class="subtitle">A Friendly Path Through Usage</p>
    <div class="pillar left" role="img" aria-label="Short white Ionic column with scrolled capital and stepped base, on the left"></div>
    <div class="pillar center" role="img" aria-label="Tall white Ionic column with scrolled capital and stepped base, standing in front in the centre"></div>
    <div class="pillar right" role="img" aria-label="Medium white Ionic column with scrolled capital and stepped base, on the right"></div>
    <p class="author-band">DOREEN CALLOWAY</p>
  </main>
</body>
</html>
```